Fast Growing Personal Injury Law Firm Needs Business Card Design

We need a business card design for a fast growing personal injury law firm in Florida. Our name is Dorian Kalvenfeld, P.A. Our practice is comprised of younger attorneys (in their 30s) that employ more modern techniques/tools than our older competition. We would prefer a look that is a modern play on a classic look. Also, we would like to continue using a color scheme that employs navy blue and kelly green (other shades of green could be fine too) as well as our "E" logo.

Industry/Entity Type

Law Firm

```html
<!DOCTYPE html>
<html lang="en">
<head>
<meta charset="utf-8">
<title>Dorian Kalvenfeld, P.A. — Business Card</title>
<link rel="stylesheet" href="https://fonts.googleapis.com/css2?family=Gelasio:wght@700&family=Lato:wght@400&display=swap">
<style>
  :root {
    --navy: #002b5f;
    --navy-deep: #0a2a6e;
    --green: #0b8a3e;
    --white: #ffffff;
    --ink: #2b2b2b;
    --stage: #4a4a4a;
  }
  * { margin: 0; padding: 0; box-sizing: border-box; }
  html, body { width: 1200px; height: 820px; overflow: hidden; }
  body { background: var(--stage); position: relative; font-family: "Lato", sans-serif; }

  .card { position: absolute; top: 258px; width: 471px; height: 270px; overflow: hidden; }
  .card-front { left: 117px; background: var(--white); }
  .card-back { left: 628px; width: 472px; background: var(--navy); }

  .brand { position: absolute; left: 21px; top: 26px; display: flex; align-items: flex-start; gap: 16px; }
  .brand-mark { width: 44px; height: 44px; background: var(--green); border: 3px solid var(--navy); flex: none; }
  .brand-name { font-family: "Gelasio", serif; font-weight: 700; font-size: 24px; line-height: 24px; color: var(--navy-deep); margin-top: -2px; }
  .brand-tagline { font-family: "Gelasio", serif; font-weight: 700; font-size: 17.5px; line-height: 22px; color: var(--green); letter-spacing: 1.2px; }

  .person { position: absolute; left: 22px; top: 93px; }
  .person-name { font-size: 16.5px; color: var(--navy); line-height: 20px; }
  .person-title { font-size: 12.5px; color: var(--ink); line-height: 18px; margin-top: 1px; }

  .address { position: absolute; left: 24px; top: 142px; font-size: 12.5px; line-height: 16px; color: var(--ink); }

  .contacts { position: absolute; left: 23px; top: 186px; list-style: none; font-size: 12.5px; line-height: 17px; color: var(--ink); }
  .contacts li { display: flex; align-items: center; gap: 5px; }
  .contacts svg { width: 11px; height: 11px; flex: none; }

  .swoosh { position: absolute; right: 0; bottom: 0; width: 471px; height: 270px; }

  .back-brand { position: absolute; left: 0; right: 0; top: 78px; display: flex; flex-direction: column; align-items: center; gap: 14px; }
  .back-mark { width: 62px; height: 62px; background: var(--green); border: 4px solid var(--white); }
  .back-name { font-family: "Lato", sans-serif; font-size: 16px; color: var(--white); }
  .back-url { position: absolute; left: 0; right: 0; top: 226px; text-align: center; font-size: 13px; color: var(--white); }
</style>
</head>
<body>
  <section class="card card-front">
    <div class="brand">
      <div class="brand-mark"></div>
      <div class="brand-text">
        <div class="brand-name">Dorian Kalvenfeld, P.A.</div>
        <div class="brand-tagline">Personal Injury Attorneys</div>
      </div>
    </div>

    <div class="person">
      <div class="person-name">Dorian Kalvenfeld</div>
      <div class="person-title">Attorney at Law</div>
    </div>

    <div class="address">
      2150 Harborview Lane Suite 410<br>
      Palm Crest, Florida 34210
    </div>

    <ul class="contacts">
      <li><svg viewBox="0 0 12 12"><circle cx="6" cy="6" r="6" fill="#002b5f"/><path d="M4 3.2l1 1.3-.6.7c.4.9 1 1.5 1.9 1.9l.7-.6 1.3 1-.6 1.1C5.6 8.4 3.6 6.4 3.4 4z" fill="#fff"/></svg>941.555.0172</li>
      <li><svg viewBox="0 0 12 12"><circle cx="6" cy="6" r="6" fill="#002b5f"/><rect x="4.2" y="2.8" width="3.6" height="6.4" rx=".6" fill="#fff"/><rect x="4.9" y="3.6" width="2.2" height="4" fill="#002b5f"/></svg>941.555.0190</li>
      <li><svg viewBox="0 0 12 12"><circle cx="6" cy="6" r="6" fill="#002b5f"/><rect x="3" y="4" width="6" height="4.2" fill="#fff"/><path d="M3 4l3 2.3L9 4" fill="none" stroke="#002b5f" stroke-width=".7"/></svg>dorian@kalvenfeldlaw.com</li>
      <li><svg viewBox="0 0 12 12"><circle cx="6" cy="6" r="6" fill="#002b5f"/><circle cx="6" cy="6" r="3.2" fill="none" stroke="#fff" stroke-width=".8"/><path d="M2.8 6h6.4M6 2.8c-1.6 1.8-1.6 4.6 0 6.4M6 2.8c1.6 1.8 1.6 4.6 0 6.4" fill="none" stroke="#fff" stroke-width=".6"/></svg>www.kalvenfeldlaw.com</li>
    </ul>

    <svg class="swoosh" viewBox="0 0 471 270" preserveAspectRatio="none" aria-hidden="true">
      <path d="M322 270 C390 250 450 210 471 150 L471 270 Z" fill="var(--green)"/>
      <path d="M334 270 C400 254 455 220 471 178 L471 270 Z" fill="var(--white)"/>
      <path d="M340 270 C404 256 458 224 471 186 L471 270 Z" fill="var(--navy)"/>
    </svg>
  </section>

  <section class="card card-back">
    <div class="back-brand">
      <div class="back-mark"></div>
      <div class="back-name">Dorian Kalvenfeld, P.A.</div>
    </div>
    <div class="back-url">www.kalvenfeldlaw.com</div>
  </section>
</body>
</html>
```